We need a logo for our business which is a dental clinic (i.e. dentistry).
We would lilke designs using the colour blue, green and black incorporating the words Corvath Dental, possibly a smile or a tooth image can be considered for incorporation in the logo.

Industry/Entity Type

Dental

```html
<!DOCTYPE html>
<html lang="en">
<head>
<meta charset="utf-8">
<title>Corvath Dental Clinic</title>
<link rel="stylesheet" href="https://fonts.googleapis.com/css2?family=Pinyon+Script&family=Michroma&display=swap">
<style>
  :root {
    --paper: #f2f2f2;
    --sky: #4dd2f7;
    --icon-blue: #3a86e8;
    --ink: #3c3c3c;
  }
  html, body {
    margin: 0;
    padding: 0;
    overflow: hidden;
    background: var(--paper);
  }
  .canvas {
    position: relative;
    width: 1200px;
    height: 748px;
    background: var(--paper);
    overflow: hidden;
  }
  .brand-dot {
    position: absolute;
    left: 108px;
    top: 172px;
    width: 100px;
    height: 100px;
    border-radius: 50%;
    background: var(--sky);
  }
  .brand-name {
    position: absolute;
    margin: 0;
    font-family: "Pinyon Script", cursive;
    font-weight: 400;
    color: var(--sky);
    line-height: 1;
    white-space: nowrap;
  }
  .brand-name--main {
    left: 240px;
    top: 150px;
    font-size: 136px;
  }
  .brand-name--sub {
    left: 540px;
    top: 300px;
    font-size: 130px;
  }
  .contact-list {
    position: absolute;
    left: 84px;
    top: 488px;
    margin: 0;
    padding: 0;
    list-style: none;
  }
  .contact-item {
    display: flex;
    align-items: center;
    height: 40px;
    margin-bottom: 36px;
  }
  .contact-icon {
    width: 40px;
    height: 40px;
    flex: none;
  }
  .contact-text {
    margin-left: 26px;
    font-family: "Michroma", sans-serif;
    font-size: 15px;
    letter-spacing: 2px;
    color: var(--ink);
  }
</style>
</head>
<body>
<main class="canvas">
  <div class="brand-dot" aria-hidden="true"></div>
  <h1 class="brand-name brand-name--main">Corvath Dental</h1>
  <p class="brand-name brand-name--sub">Clinic</p>

  <ul class="contact-list">
    <li class="contact-item">
      <svg class="contact-icon" viewBox="0 0 40 40" aria-label="Phone">
        <rect x="10" y="6" width="18" height="32" rx="4" fill="var(--icon-blue)"/>
        <rect x="13" y="10" width="12" height="12" rx="1" fill="var(--paper)"/>
        <rect x="22" y="1" width="3" height="6" fill="var(--icon-blue)"/>
        <circle cx="19" cy="30" r="2.5" fill="var(--paper)"/>
      </svg>
      <span class="contact-text">2014 2015 2016</span>
    </li>
    <li class="contact-item">
      <svg class="contact-icon" viewBox="0 0 40 40" aria-label="Address">
        <path d="M20 3 L2 19 L6 19 L6 37 L16 37 L16 26 L24 26 L24 37 L34 37 L34 19 L38 19 Z" fill="var(--icon-blue)"/>
      </svg>
      <span class="contact-text">at home at home</span>
    </li>
    <li class="contact-item">
      <svg class="contact-icon" viewBox="0 0 40 40" aria-label="Email">
        <rect x="3" y="8" width="34" height="24" fill="none" stroke="var(--icon-blue)" stroke-width="3"/>
        <path d="M4 9 L20 23 L36 9" fill="none" stroke="var(--icon-blue)" stroke-width="3"/>
      </svg>
      <span class="contact-text">mailme once in a while</span>
    </li>
  </ul>
</main>
</body>
</html>
```